Automotive component supplier needs a business card design

We need a business card design for our company called Velran Global Components Ltd based in the UK. We are a supplier of interior and exterior components to premium car manufacturers such as Corvel Ashby, Hadley Fenn, Marquist and Tavarelli. We would like to see a modern business card design that uses the colour blue.

Target Market(s)

Premium automotive car manufacturers.

Industry/Entity Type

Automotive

Contact Information for Business Card

Company Name : Velran Global Components Limited
Address: 17 Marlow Yard, Upper Heath, Warwick, CV31 8QL, United Kingdom
Web Address : www.velrancomponents-example.co.uk

Font styles to use
Other font styles liked:
• Helvetica

Colors
3176b5
0255a3
85acd3
cfdeed
cee9f5
85cae6
34a6d7
0692cd
9bcb3c

Requirements
Must have
• Clear company logo and a mixture of blue colours.
Nice to have
• A high quality modern image.
Should not have
• Multiple colours.

```html
<!DOCTYPE html>
<html lang="en">
<head>
<meta charset="utf-8">
<title>Velran Global Components – Business Card</title>
<link href="https://fonts.googleapis.com/css2?family=Lato:wght@400;700;900&display=swap" rel="stylesheet">
<style>
  :root{
    --brand-blue:#0a8fd0;
    --deep-blue:#0a78c2;
    --lime:#9bcb3c;
    --ink:#1d1d1f;
    --paper:#ffffff;
    --backdrop:#e9edf1;
  }
  *{margin:0;padding:0;box-sizing:border-box}
  html,body{width:1200px;height:800px;overflow:hidden}
  body{
    background:var(--backdrop);
    font-family:'Lato',Helvetica,Arial,sans-serif;
    display:flex;flex-direction:column;align-items:center;justify-content:center;gap:36px;
  }
  .card{
    position:relative;width:610px;height:349px;border-radius:4px;overflow:hidden;
    box-shadow:0 6px 18px rgba(0,0,0,.12);
  }
  .wordmark__square{flex:none;width:16px;height:16px;background:var(--lime);border-radius:2px}
  .wordmark__name{font-weight:900;letter-spacing:.5px;line-height:1.05}

  /* back side */
  .card--back{background:var(--brand-blue)}
  .card--back .wordmark{
    position:absolute;left:0;right:0;top:128px;
    display:flex;align-items:center;justify-content:center;gap:12px;
  }
  .card--back .wordmark__name{color:var(--paper);font-size:40px}
  .card--back .web{
    position:absolute;left:0;right:0;bottom:40px;text-align:center;
    color:var(--lime);font-size:15px;letter-spacing:1.5px;
  }

  /* front side */
  .card--front{background:var(--paper)}
  .card--front .wordmark{
    position:absolute;left:40px;top:44px;width:310px;
    display:flex;align-items:center;gap:12px;
  }
  .card--front .wordmark__name{color:var(--brand-blue);font-size:30px}
  .person{position:absolute;right:40px;top:112px;text-align:right}
  .person__name{color:var(--deep-blue);font-weight:700;font-size:24px;line-height:1.1}
  .person__role{color:var(--ink);font-size:15px;margin-top:2px}
  .address{
    position:absolute;left:40px;top:150px;color:var(--ink);font-size:17px;line-height:1.3;font-style:normal;
  }
  .contacts{position:absolute;left:40px;top:222px;list-style:none;color:var(--ink);font-size:17px;line-height:1.4}
  .contacts li{display:flex;align-items:center;gap:12px}
  .contacts svg{width:16px;height:16px;fill:var(--brand-blue)}
  .footer-band{position:absolute;left:0;bottom:0;width:610px;height:60px}
  .card--front .web{
    position:absolute;right:14px;bottom:15px;color:var(--paper);font-size:13px;letter-spacing:.3px;white-space:nowrap;
  }
</style>
</head>
<body>

<section class="card card--back" aria-label="Business card back">
  <div class="wordmark">
    <span class="wordmark__square"></span>
    <span class="wordmark__name">Velran Global Components</span>
  </div>
  <p class="web">www.velrancomponents-example.co.uk</p>
</section>

<section class="card card--front" aria-label="Business card front">
  <div class="wordmark">
    <span class="wordmark__square"></span>
    <span class="wordmark__name">Velran Global<br>Components</span>
  </div>

  <div class="person">
    <p class="person__name">Daniel Orrick</p>
    <p class="person__role">Manager</p>
  </div>

  <address class="address">
    17 Marlow Yard, Upper Heath<br>
    Warwick, CV31 8QL<br>
    United Kingdom
  </address>

  <ul class="contacts">
    <li>
      <svg viewBox="0 0 24 24" aria-hidden="true"><path d="M6.6 10.8a15.1 15.1 0 0 0 6.6 6.6l2.2-2.2a1 1 0 0 1 1-.25 11.4 11.4 0 0 0 3.6.57 1 1 0 0 1 1 1V20a1 1 0 0 1-1 1A17 17 0 0 1 3 4a1 1 0 0 1 1-1h3.5a1 1 0 0 1 1 1c0 1.25.2 2.45.57 3.6a1 1 0 0 1-.25 1z"/></svg>
      512 004 7300
    </li>
    <li>
      <svg viewBox="0 0 24 24" aria-hidden="true"><path d="M7 2h10a2 2 0 0 1 2 2v16a2 2 0 0 1-2 2H7a2 2 0 0 1-2-2V4a2 2 0 0 1 2-2zm0 3v12h10V5zm5 13.5a1 1 0 1 0 0 2 1 1 0 0 0 0-2z"/></svg>
      512 004 7301
    </li>
    <li>
      <svg viewBox="0 0 24 24" aria-hidden="true"><path d="M2 5h20v14H2zm2 2v.5l8 5 8-5V7zm0 2.8V17h16V9.8l-8 5z"/></svg>
      info@velrancomponents-example.co.uk
    </li>
  </ul>

  <svg class="footer-band" viewBox="0 0 610 60" preserveAspectRatio="none" aria-hidden="true">
    <path d="M0 42 L328 42 C344 42 346 14 364 14 L610 14 L610 60 L0 60 Z" fill="var(--brand-blue)"/>
    <path d="M0 35 L324 35 C334 35 338 28 343 22" fill="none" stroke="var(--lime)" stroke-width="4"/>
  </svg>
  <p class="web">www.velrancomponents-example.co.uk</p>
</section>

</body>
</html>
```